Professional & attention grabbing.

A business card design, front and back. I already have a logo I will attach, but I am open to something new as well.
Things to include:
Name:
Title:
Phone:
Email:
Wanting something that is professional but attention grabbing.
Also we do a lot of work using drones on natural gas pipelines (leading the future)if you want to include any of that. I'm open to ideas.
Target Market(s)
Natural gas transmission industry / greenhouse gas mitigation industry
Industry/Entity Type
Business
Colors
Designer to choose colors to be used in the design.
Look and feel
Each slider illustrates characteristics of the customer's brand and the style your logo design should communicate.

```html
<!DOCTYPE html>
<html lang="en">
<head>
<meta charset="utf-8">
<title>Kestrel Field Inspections – Business Card</title>
<link href="https://fonts.googleapis.com/css2?family=Roboto+Condensed:ital,wght@0,400;0,700;1,700&display=swap" rel="stylesheet">
<style>
  :root{
    --stage:#1b1b1c;
    --card-white:#ffffff;
    --card-dark:#3a3a3b;
    --map-tone:#454547;
    --brand-red:#c21f26;
    --ink:#2b2b2d;
    --ink-soft:#444446;
    --white:#ffffff;
  }
  *{box-sizing:border-box;margin:0;padding:0}
  html,body{width:1200px;height:1000px;overflow:hidden;background:var(--stage)}
  body{font-family:"Roboto Condensed",Arial,sans-serif;position:relative}

  .card{position:absolute;left:250px;width:700px;height:400px;border-radius:18px;overflow:hidden}
  .card-front{top:60px;background:var(--card-white)}
  .card-back{top:540px;background:var(--card-dark)}

  /* brand lockup */
  .brand{position:absolute;display:flex;align-items:center;gap:12px}
  .brand-mark{width:22px;height:22px;background:var(--brand-red)}
  .brand-name{font-weight:700;text-transform:uppercase;letter-spacing:1px;line-height:1}
  .card-front .brand{left:48px;top:52px}
  .card-front .brand-name{font-size:30px;color:var(--ink)}
  .card-back .brand{left:50%;top:50%;transform:translate(-50%,-50%)}
  .card-back .brand-mark{width:34px;height:34px}
  .card-back .brand-name{font-size:46px;color:var(--white)}

  .divider{position:absolute;left:70px;top:150px;width:420px;height:2px;background:var(--ink)}

  .contact{position:absolute;left:48px;top:172px;list-style:none;font-size:19px;color:var(--ink-soft)}
  .contact li{display:flex;align-items:center;gap:10px;margin-bottom:6px}
  .contact svg{width:16px;height:16px;fill:var(--brand-red)}

  .person{position:absolute;right:70px;top:258px;text-align:right}
  .person-name{font-size:28px;font-weight:700;font-style:italic;color:var(--brand-red);text-transform:uppercase;letter-spacing:1px}
  .person-title{font-size:18px;color:var(--ink);text-transform:uppercase;letter-spacing:1px;border-top:2px solid var(--ink);display:inline-block;padding-top:2px;margin-top:2px}

  .red-band{position:absolute;left:0;bottom:0;width:700px;height:140px}

  .world-map{position:absolute;left:90px;top:60px;width:520px;height:280px;border-radius:40%;background:radial-gradient(ellipse at center,var(--map-tone) 0%,var(--card-dark) 70%)}
</style>
</head>
<body>

<section class="card card-front" aria-label="Business card front">
  <div class="brand">
    <span class="brand-mark"></span>
    <span class="brand-name">Kestrel Field Inspections</span>
  </div>

  <div class="divider"></div>

  <ul class="contact">
    <li>
      <svg viewBox="0 0 16 16" aria-hidden="true"><path d="M3 1h3l1 4-2 1c1 2 3 4 5 5l1-2 4 1v3c0 1-1 2-2 2C7 15 1 9 1 3c0-1 1-2 2-2z"/></svg>
      000 000 0000
    </li>
    <li>
      <svg viewBox="0 0 16 16" aria-hidden="true"><path d="M1 3h14v10H1z M1 3l7 6 7-6" stroke="#fff" stroke-width="1.2"/></svg>
      info@kestrelfield.com
    </li>
  </ul>

  <div class="person">
    <div class="person-name">Daniel Reyes</div>
    <div class="person-title">Founder</div>
  </div>

  <svg class="red-band" viewBox="0 0 700 140" preserveAspectRatio="none" aria-hidden="true">
    <path d="M0 30 L330 92 L0 40 Z" fill="var(--brand-red)"/>
    <path d="M0 52 L340 104 C380 110 400 120 430 130 L560 128 C600 126 620 110 650 108 L700 106 L700 140 L0 140 Z" fill="var(--brand-red)"/>
  </svg>
</section>

<section class="card card-back" aria-label="Business card back">
  <div class="world-map" role="img" aria-label="Faint dotted world map in the background"></div>
  <div class="brand">
    <span class="brand-mark"></span>
    <span class="brand-name">Kestrel Field Inspections</span>
  </div>
</section>

</body>
</html>
```